Young, modern, highly skilled carpenter needs business card design

I need a business card design for my construction business. Its called 'Barlow Construction Services'. Im looking for a ultra modern design that incorporates B C S, the first letters of the name with only a subtle reference to carpentry. The design should reflect my high quality work and eye for detail. i have also uploaded some exmaple designs i like.

Industry/Entity Type

Construction

Requirements
Must have
• Name of business, my name, mobile number, ABN number, email address
Nice to have
• A logo incorporating the name of the business

```html
<!DOCTYPE html>
<html lang="en">
<head>
<meta charset="UTF-8">
<title>Barlow Construction Services – Business Card</title>
<link href="https://fonts.googleapis.com/css2?family=Source+Sans+3:wght@400;700&display=swap" rel="stylesheet">
<style>
  :root {
    --backdrop: #7d8d8d;
    --card: #ffffff;
    --teal: #6a9aa0;
    --yellow: #f5cf14;
    --shadow: rgba(0, 0, 0, 0.75);
  }
  * { margin: 0; padding: 0; box-sizing: border-box; }
  html, body {
    width: 1200px;
    height: 900px;
    overflow: hidden;
    background: var(--backdrop);
    font-family: "Source Sans 3", Arial, sans-serif;
  }
  .canvas { position: relative; width: 1200px; height: 900px; }
  .card {
    position: absolute;
    background: var(--card);
    box-shadow: 6px 6px 4px var(--shadow);
  }
  .card--front { left: 335px; top: 60px; width: 545px; height: 369px; }
  .card--back  { left: 335px; top: 460px; width: 547px; height: 376px; }

  .brand-name {
    position: absolute;
    color: var(--teal);
    white-space: nowrap;
  }
  .card--front .brand-name {
    left: 64px;
    top: 226px;
    font-size: 100px;
    font-weight: 700;
    line-height: 1;
    letter-spacing: 4px;
  }
  .card--back .brand-name {
    left: 68px;
    top: 304px;
    font-size: 19px;
    font-weight: 400;
    line-height: 24px;
  }

  .contact {
    position: absolute;
    left: 67px;
    top: 48px;
    color: var(--teal);
    font-size: 20px;
    line-height: 27px;
  }
  .contact__name { color: var(--yellow); font-weight: 700; }
  .contact__divider { color: var(--yellow); }
</style>
</head>
<body>
  <main class="canvas">
    <section class="card card--front" aria-label="Card front">
      <p class="brand-name">BCS</p>
    </section>

    <section class="card card--back" aria-label="Card back">
      <div class="contact">
        <p class="contact__name">Liam Barlow</p>
        <p class="contact__email">liam_barlow@mailbox.net</p>
        <p class="contact__numbers">0412 555 018 <span class="contact__divider">//</span> ABN 12 345 678 901</p>
      </div>
      <p class="brand-name">Barlow Construction Services</p>
    </section>
  </main>
</body>
</html>
```